Business Card Design

New business card design

Target Market(s)

Residential & Commercial Property Managers

Industry/Entity Type

Plumbing Services

Contact Information for Business Card

Name - Rowan Keddle, title - Director, Phone Number - 0431 286 517, email - rowan@tbk-plumbing.com.au, Company ABN - 73 215 904 386,

Font styles to use
Sans Serif

Colors
0054AA
0677BA
7BADD7
CADEEF
E8F1F8

```html
<!DOCTYPE html>
<html lang="en">
<head>
<meta charset="utf-8">
<title>TBK Plumbing Services – Business Card</title>
<link href="https://fonts.googleapis.com/css2?family=Montserrat:wght@400;500;700&display=swap" rel="stylesheet">
<style>
  :root {
    --backdrop: #2b2c2e;
    --card-white: #ffffff;
    --navy: #1c2128;
    --sky: #2aa8e0;
    --text-light: #ffffff;
  }
  * { box-sizing: border-box; margin: 0; padding: 0; }
  html, body { width: 1200px; height: 880px; overflow: hidden; }
  body {
    background: var(--backdrop);
    font-family: "Montserrat", sans-serif;
    position: relative;
  }
  .card {
    position: absolute;
    left: 285px;
    width: 630px;
    height: 360px;
    border-radius: 26px;
    background: var(--card-white);
    overflow: hidden;
  }
  .card--front { top: 60px; }
  .card--back { top: 460px; }

  .brand {
    position: absolute;
    display: flex;
    align-items: center;
    gap: 12px;
    color: var(--navy);
    font-weight: 500;
    white-space: nowrap;
  }
  .brand__dot {
    border-radius: 50%;
    background: var(--sky);
    flex: none;
  }
  .card--front .brand {
    left: 50%; top: 50%;
    transform: translate(-50%, -50%);
    font-size: 36px;
  }
  .card--front .brand__dot { width: 26px; height: 26px; }
  .card--back .brand {
    right: 40px; top: 48px;
    font-size: 24px;
  }
  .card--back .brand__dot { width: 18px; height: 18px; }

  .wave { position: absolute; inset: 0; width: 630px; height: 360px; }

  .contact {
    position: absolute;
    left: 56px;
    top: 232px;
    color: var(--text-light);
  }
  .contact__accent {
    position: absolute;
    left: 30px; top: 236px;
    width: 8px; height: 54px;
    background: var(--sky);
  }
  .contact__name {
    color: var(--sky);
    font-weight: 700;
    font-size: 26px;
    line-height: 1.1;
  }
  .contact__title {
    font-size: 17px;
    margin-top: 2px;
  }
  .contact__lines { margin-top: 14px; font-size: 15px; }
  .contact__line { display: flex; align-items: center; gap: 8px; margin-top: 4px; }
  .contact__line svg { width: 15px; height: 15px; flex: none; }

  .abn {
    position: absolute;
    right: 34px; top: 176px;
    text-align: right;
    color: var(--text-light);
    font-size: 15px;
    line-height: 1.4;
  }
</style>
</head>
<body>
  <section class="card card--front">
    <div class="brand"><span class="brand__dot"></span>TBK Plumbing Services</div>
  </section>

  <section class="card card--back">
    <svg class="wave" viewBox="0 0 630 360" aria-hidden="true">
      <path fill="#2aa8e0" d="M0,222 C120,132 250,130 420,122 C530,116 600,90 630,30 L630,360 L0,360 Z"/>
      <path fill="#ffffff" d="M0,234 C120,144 250,142 420,134 C530,128 600,102 630,50 L630,360 L0,360 Z"/>
      <path fill="#1c2128" d="M0,242 C120,152 250,150 420,142 C530,136 600,110 630,60 L630,360 L0,360 Z"/>
    </svg>

    <div class="brand"><span class="brand__dot"></span>TBK Plumbing Services</div>

    <div class="abn">Company ABN<br>- 73 215 904 386</div>

    <span class="contact__accent"></span>
    <div class="contact">
      <p class="contact__name">Rowan Keddle</p>
      <p class="contact__title">Director</p>
      <div class="contact__lines">
        <p class="contact__line">
          <svg viewBox="0 0 24 24"><path fill="#2aa8e0" d="M6.6 10.8a15.1 15.1 0 0 0 6.6 6.6l2.2-2.2c.3-.3.7-.4 1-.2 1.1.4 2.3.6 3.6.6.6 0 1 .4 1 1V20c0 .6-.4 1-1 1A17 17 0 0 1 3 4c0-.6.4-1 1-1h3.5c.6 0 1 .4 1 1 0 1.3.2 2.5.6 3.6.1.3 0 .7-.2 1z"/></svg>
          0431 286 517
        </p>
        <p class="contact__line">
          <svg viewBox="0 0 24 24"><path fill="#2aa8e0" d="M3 5h18c.6 0 1 .4 1 1v12c0 .6-.4 1-1 1H3c-.6 0-1-.4-1-1V6c0-.6.4-1 1-1zm1 2.2V17h16V7.2l-8 5.3z"/></svg>
          rowan@tbk-plumbing.com.au
        </p>
      </div>
    </div>
  </section>
</body>
</html>
```